Tuition Center Website

We need a new web site for a tutoring company based in sydney.

We only teach senior highschool students and pride ourselves on building the students abilities to think their way through life.

I would like a bright and vibrant website that looks professional and modern.
It needs to look simple and neat but also have the functionality we need.
Images and flash would be good.

Please keep in mind that the site must be appealing to a younger audience.

We need a multipage website with the following navigation bars:

1.Home (As logo not "home" button)
I would like a news box/ticker somewhere that can stream our chatterbook and pipstream feeds and also any news updates we want to put up.
Subscribe to newsletter button.

2. About us.
This needs to be a pull down into:
-What we do
-Why we do it
-How we do it

3. Courses
Pulldown into:
-Maths
-English
-Science
(we may need to attach extra pages behind these e.g. Courses/Science/Physics or Courses/Science/Chemistry and possibly add a link to a new zandlo form)

4. Inspired
This page is like a blog page where we can upload videos, links to articles that we find to be inspiring and hopefully will inspire others.

5. Inspire
This is a recruitment page. Only content here.

6. Contact us.
Mapquill map widget and a 'contact us' form

* Our branding requires green close to #12FF3D

***Please have a look at the current website.
@ www.velmorlearning.com.au

Thanks everybody hope the revision of my brief is better and more informative than my last one

Target Market(s)

senior highschool students aged 15-19, parents ( to a lesser degree)

Industry/Entity Type

It Company

Requirements
Must have
• Ability to change content on pages.

The green doesn't have to be everywhere, but it must be obvious that it is our colour.

Nice to have
• Sites with a nicer mix of images and flash will be given more consideration. But then again, if you amaze us, you amaze us and we will go with your design.
Should not have
• Should stay away from ocre, brown colours and serif fonts.

```html
<!DOCTYPE html>
<html lang="en">
<head>
<meta charset="utf-8">
<title>Velmor Learning – HSC Coaching</title>
<link href="https://fonts.googleapis.com/css2?family=Ubuntu:wght@300;400;500&family=Ubuntu+Condensed&display=swap" rel="stylesheet">
<style>
:root{
  --page:#6fdc3a;
  --brand:#22c93a;
  --brand-light:#3fe25a;
  --accent-text:#4cbf1e;
  --ink:#333;
  --white:#fff;
  --footer:#0d0d0d;
  --rule:#ddd;
}
*{box-sizing:border-box;margin:0;padding:0}
html,body{width:1064px;height:1200px;overflow:hidden}
body{position:relative;background:var(--page);font-family:"Ubuntu",sans-serif;font-weight:300;color:var(--ink)}
.abs{position:absolute}
a{color:inherit;text-decoration:none}

.utility-links{right:190px;top:14px;font-size:11px;color:#1d3d10;white-space:nowrap}
.utility-links span{margin:0 4px}
.like-chip{left:885px;top:14px;font-size:10px;background:var(--white);border:1px solid #ccc;padding:1px 5px;color:#3b5998}
.like-count{left:930px;top:14px;font-size:10px;background:var(--white);border:1px solid #ccc;padding:1px 4px}

.header-panel{left:88px;top:45px;width:888px;height:205px;background:var(--white);border-radius:3px}
.brand-square{left:112px;top:64px;width:128px;height:115px;background:var(--brand-light)}
.brand-name{left:96px;top:183px;width:166px;text-align:center;font-size:27px;line-height:27px;font-weight:500;color:var(--brand)}
.search-box{left:755px;top:70px;width:195px;height:32px;border:1px solid var(--rule);border-radius:3px;background:var(--white);box-shadow:0 3px 4px rgba(0,0,0,.08);font-size:9px;color:#555;padding:11px 14px}
.search-box svg{position:absolute;right:10px;top:8px}
.contact-lines{right:106px;top:136px;text-align:right;font-size:12px;line-height:19px;font-style:normal}
.contact-lines .hl{color:var(--accent-text)}

.main-nav{left:262px;top:193px;width:709px;height:48px;background:linear-gradient(#34d84a,#12b12c);border:1px solid #0e9b24;border-radius:3px;display:flex;align-items:center;justify-content:space-between;padding:0 18px 0 15px;font-family:"Ubuntu Condensed","Ubuntu",sans-serif;font-size:14px;font-weight:400;color:var(--white);white-space:nowrap;text-shadow:0 1px 1px rgba(0,0,0,.25)}

.hero{left:88px;top:255px;width:888px;height:391px;background:var(--white);border-radius:3px;overflow:hidden}
.hero-photo{left:0;top:0;width:620px;height:391px;background:linear-gradient(90deg,#b08a6c 0%,#d9c2ad 30%,#eee5dc 60%,#fbf9f7 88%,rgba(255,255,255,0) 100%)}
.hero-title{left:614px;top:315px;font-size:34px;font-weight:300;color:#444}
.hero-sub{left:614px;top:358px;font-size:16px;color:var(--accent-text)}
.hero-copy{left:614px;top:390px;width:310px;font-size:11.4px;line-height:19.5px;color:#666;text-align:justify}
.btn{background:linear-gradient(#45e05c,#14b42d);border:1px solid #0e9b24;border-radius:3px;color:var(--white);font-family:"Ubuntu",sans-serif;font-weight:500;text-align:center;white-space:nowrap;text-shadow:0 1px 1px rgba(0,0,0,.25);box-shadow:0 3px 5px rgba(0,0,0,.15)}
.enquiry-btn{left:710px;top:520px;width:204px;height:39px;font-size:21px;line-height:37px}
.slide-dots{left:825px;top:605px;display:flex;gap:8px}
.slide-dots i{width:11px;height:11px;border-radius:50%;background:var(--brand-light);border:1px solid #2fae2a}
.slide-dots i.on{background:#000;border-color:#000}

.card{background:var(--white);border-radius:2px;box-shadow:0 6px 8px -6px rgba(0,0,0,.35)}
.card h2{position:absolute;font-weight:300;font-size:23px;line-height:26px;color:#333;white-space:nowrap}
.card p{position:absolute;font-size:11px;line-height:16px;color:#666;text-align:justify}
.card .btn{position:absolute;height:30px;font-size:13px;line-height:28px}
.testimonials{left:90px;top:667px;width:267px;height:234px}
.trial{left:398px;top:667px;width:268px;height:234px}
.blog{left:707px;top:667px;width:267px;height:234px}
.trial-badge{position:absolute;left:32px;top:90px;width:55px;height:58px;background:#7bd04a}
.blog-title{position:absolute;left:26px;top:72px;width:221px;font-weight:300;font-size:14.5px;line-height:18px;color:#333}
.blog-title span{display:block;white-space:nowrap}
.blog-title .spread{text-align:justify;text-align-last:justify}

.subscribe{left:89px;top:917px;width:436px;height:148px}
.news{left:538px;top:917px;width:437px;height:148px}
.news-dots{position:absolute;left:385px;top:18px;display:flex;gap:8px}
.news-dots i{width:11px;height:11px;border-radius:50%;background:var(--brand-light)}
.news-dots i.on{background:#000}
.field{position:absolute;left:22px;top:54px;width:292px;height:31px;border:1px solid var(--rule);border-radius:3px;font-size:9px;padding:11px 14px;color:#555;box-shadow:0 2px 3px rgba(0,0,0,.06)}
.news-photo{position:absolute;left:25px;top:56px;width:89px;height:62px;background:linear-gradient(135deg,#8a5a3a,#c79a6d 50%,#e8ddd0);border:2px solid #eee}
.news-copy{position:absolute;left:123px;top:62px;width:297px;font-size:12px;line-height:14px;color:#666}
.news-date{position:absolute;left:123px;top:105px;font-size:10px;color:#999}
.share-row{position:absolute;left:140px;top:126px;display:flex;gap:14px;font-size:7.5px;color:#333}
.share-row span{border:1px solid #bbb;background:#f3f3f3;padding:1px 4px;border-radius:2px}

.site-footer{left:0;top:1075px;width:1064px;height:125px;background:var(--footer);color:var(--white);font-size:11.5px}
.social{position:absolute;left:118px;top:26px;display:flex;gap:12px;font-size:11px;align-items:center}
.social span{display:flex;align-items:center;gap:4px}
.social i{width:10px;height:10px;border-radius:50%;background:var(--white)}
.footer-nav{position:absolute;left:118px;top:63px;display:flex;gap:18px;white-space:nowrap}
.legal{position:absolute;left:118px;top:84px;white-space:nowrap}
.footer-contact{position:absolute;right:113px;top:25px;text-align:right;line-height:16px}
.footer-contact h4{font-weight:300;font-size:13.5px;color:#7ed23c;margin-bottom:9px}
</style>
</head>
<body>

<nav class="abs utility-links">Past HSC Exam Papers<span>|</span>State Students Portal<span>|</span>TAC Admissions<span>|</span>HSC Study Hub [Study Resources]<span>|</span>Help for Study Stress<span>|</span></nav>
<div class="abs like-chip">Like</div>
<div class="abs like-count">3k</div>

<header>
  <div class="abs header-panel"></div>
  <div class="abs brand-square"></div>
  <div class="abs brand-name">velmor<br>learning</div>
  <div class="abs search-box">Search
    <svg width="16" height="16" viewBox="0 0 16 16"><circle cx="6.5" cy="6.5" r="5" fill="none" stroke="#888" stroke-width="1.6"/><line x1="10.3" y1="10.3" x2="15" y2="15" stroke="#888" stroke-width="2"/></svg>
  </div>
  <address class="abs contact-lines">Street: 48 Larkfield Rd Ashgrove NSW 2190<br>Phone: <span class="hl">(02) 5550 1294</span> &nbsp;|&nbsp; Email: <span class="hl">learn@velmorlearning.com.au</span></address>
  <nav class="abs main-nav"><a>HOME</a><a>ABOUT US</a><a>FIND US</a><a>GET IN TOUCH</a><a>RECENT NEWS</a><a>YEAR 10 CLASSES</a><a>YR 11 &amp; 12 HSC CLASSES</a></nav>
</header>

<section class="abs hero">
  <div class="abs hero-photo" role="img" aria-label="Photo of students studying and writing notes at a desk"></div>
</section>
<h1 class="abs hero-title">i am velmor.</h1>
<p class="abs hero-sub">real HSC coaching &amp; mentoring.</p>
<p class="abs hero-copy">The HSC help you need, in the years you need it. We offer small classes, individualised attention and genuine care for each student. It's different - in a good way. Feel free to find out more about us, and let us know if there's any way we can help you on your journey.</p>
<a class="abs btn enquiry-btn">ENQUIRY NOW</a>
<div class="abs slide-dots"><i class="on"></i><i></i><i></i><i></i></div>

<section class="abs card testimonials">
  <h2 style="left:26px;top:14px">What Our<br>Students Say</h2>
  <p style="left:33px;top:97px;width:213px">I like the teachers and that we can study there; it's comfortable. They don't help you just with study, but other things too, and it's really easy to ask the teachers questions about stuff you don't know.</p>
  <a class="btn" style="left:148px;top:183px;width:101px">Read More &gt;&gt;</a>
</section>

<section class="abs card trial">
  <h2 style="left:31px;top:14px">Ask for your<br>free trial lesson.</h2>
  <div class="trial-badge"></div>
  <p style="left:97px;top:97px;width:150px">Because we believe you shouldn't have to sign up until you see what it's actually like. Call or email us now!</p>
  <a class="btn" style="left:122px;top:180px;width:126px">Send an Enquiry &gt;&gt;</a>
</section>

<section class="abs card blog">
  <h2 style="left:24px;top:14px">Blog</h2>
  <h3 class="blog-title"><span class="spread">How Coaching Can Impact</span><span>Teachers, Principals, and Students</span></h3>
  <p style="left:26px;top:112px;width:221px">Mara Quinlan MARCH 25, 2013<br>The following is an excerpt from my new book, The Craft of Guidance: Effective Strategies for School Transformation.</p>
  <a class="btn" style="left:146px;top:183px;width:101px">Read More &gt;&gt;</a>
</section>

<section class="abs card subscribe">
  <h2 style="left:23px;top:13px">Subscribe your News Letter</h2>
  <div class="field">Search</div>
  <a class="btn" style="left:321px;top:55px;width:101px;font-size:16px">Subscribe</a>
  <p style="left:26px;top:101px;width:396px;font-size:12px;line-height:14px">Lorem ipsum dolor sit amet, consectetur adipisicing elit, sed do eiusmod tempor incididunt ut labore et dolore magna aliqua.</p>
</section>

<section class="abs card news">
  <h2 style="left:20px;top:13px">Recent News</h2>
  <div class="news-dots"><i class="on"></i><i></i></div>
  <div class="news-photo" role="img" aria-label="Photo of a student in a school library"></div>
  <div class="news-copy">Lorem ipsum dolor sit amet, consectetur adipisicing elit, sed do eiusmod tempor incididunt ut labore et dolore magna aliqua. Ut enim ad minim veniam, qui</div>
  <div class="news-date">Mar-29-2013</div>
  <div class="share-row"><span>Post 0</span><span>+1 0</span><span>Share 0</span><span>Like 4</span><span>Pin</span></div>
</section>

<footer class="abs site-footer">
  <div class="social"><span><i></i>pipstream</span><span>chatterbook</span><span>Mapquill</span><span>RSS</span></div>
  <nav class="footer-nav"><a>Home</a><a>About Us</a><a>Find Us</a><a>Get in Touch</a><a>Recent News</a><a>Year 10 Classes</a><a>Yr 11 &amp; 12 HSC Classes</a></nav>
  <div class="legal">© &nbsp;2013 Velmor Learning &nbsp;&nbsp;| &nbsp;Privacy Policy | Terms &amp; conditions</div>
  <div class="footer-contact">
    <h4>Contact Us</h4>
    Street: 48 Larkfield Rd Ashgrove NSW 2190<br>Phone: (02) 5550 1294<br>Email: learn@velmorlearning.com.au
  </div>
</footer>

</body>
</html>
```